Business cards to launch an education platform

Hi,
I am looking at having new business cards designed.
I am a startup, developing a web platform for schools and university, the education world. It's an online assessment system.
I would like a card that looks classy, and that is using the colors and the font of my logo.

I have attached:
1) my logo
2) A business card that I have designed quickly so you can have all the information required in the card, but I really don't like it.
3) The font that I am using (Lato Regular) to design my web platform
4) Some screenshots of my web platform so you can have a look at the style that I have.

Target Market(s)

Major market: Education system: Schools and university
Minor markets: Business in general

Industry/Entity Type

Business

Contact Information for Business Card

Clara Fenwick
Director

M: 0437 518 902
E: clara.fenwick@amberLoomSystems.com.au

Requirements
Must have
• The colors of my logo

```html
<!DOCTYPE html>
<html lang="en">
<head>
<meta charset="utf-8">
<title>Amber Loom Systems — Business Cards</title>
<link rel="stylesheet" href="https://fonts.googleapis.com/css2?family=Lato:wght@400;700&display=swap">
<style>
  :root {
    --navy: #1b3f73;
    --sky: #29aee3;
    --ocean: #0a5ea8;
    --ocean-light: #5cc6de;
    --paper: #ffffff;
    --backdrop: #eef1f4;
    --shadow: rgba(20, 30, 50, 0.28);
  }
  * { box-sizing: border-box; margin: 0; padding: 0; }
  html, body {
    width: 1189px;
    height: 1200px;
    overflow: hidden;
    background: var(--backdrop);
    font-family: "Lato", sans-serif;
  }
  .sheet {
    position: relative;
    width: 1189px;
    height: 1200px;
  }
  .card {
    position: absolute;
    left: 166px;
    width: 856px;
    height: 488px;
    background: var(--paper);
    box-shadow: 6px 8px 14px var(--shadow);
    overflow: hidden;
  }
  .card--front { top: 67px; }
  .card--back { top: 627px; }

  /* Front */
  .brand-front {
    position: absolute;
    left: 0; right: 0;
    top: 188px;
    display: flex;
    align-items: center;
    justify-content: center;
    gap: 18px;
  }
  .brand-mark {
    width: 34px;
    height: 34px;
    background: var(--ocean);
    flex: none;
  }
  .brand-name {
    color: var(--navy);
    font-weight: 400;
    letter-spacing: 0.06em;
    white-space: nowrap;
  }
  .brand-front .brand-name { font-size: 50px; }

  /* Back */
  .accent-panel {
    position: absolute;
    top: 0;
    right: 0;
    width: 230px;
    height: 488px;
    background: linear-gradient(90deg, var(--ocean-light), var(--ocean));
  }
  .brand-back {
    position: absolute;
    left: 54px;
    top: 100px;
    display: flex;
    align-items: center;
    gap: 14px;
  }
  .brand-back .brand-mark { width: 26px; height: 26px; }
  .brand-back .brand-name { font-size: 38px; }

  .person {
    position: absolute;
    left: 54px;
    top: 276px;
  }
  .person__name {
    color: var(--navy);
    font-weight: 700;
    font-size: 33px;
    line-height: 1.05;
    letter-spacing: -0.01em;
  }
  .person__role {
    color: var(--sky);
    font-size: 21px;
    line-height: 1.1;
  }
  .contact {
    position: absolute;
    left: 54px;
    top: 375px;
    list-style: none;
  }
  .contact__item {
    display: flex;
    align-items: center;
    gap: 10px;
    height: 30px;
    color: var(--navy);
    font-size: 22px;
  }
  .contact__icon {
    width: 24px;
    height: 24px;
    flex: none;
  }
</style>
</head>
<body>
<main class="sheet">

  <section class="card card--front" aria-label="Business card front">
    <div class="brand-front">
      <span class="brand-mark" aria-hidden="true"></span>
      <span class="brand-name">Amber Loom Systems</span>
    </div>
  </section>

  <section class="card card--back" aria-label="Business card back">
    <div class="accent-panel" role="img" aria-label="Decorative blue sweeping band on the right edge of the card"></div>

    <div class="brand-back">
      <span class="brand-mark" aria-hidden="true"></span>
      <span class="brand-name">Amber Loom Systems</span>
    </div>

    <div class="person">
      <p class="person__name">Clara Fenwick</p>
      <p class="person__role">Director</p>
    </div>

    <ul class="contact">
      <li class="contact__item">
        <svg class="contact__icon" viewBox="0 0 24 24" aria-hidden="true">
          <rect width="24" height="24" fill="var(--ocean)"/>
          <rect x="8" y="3" width="8" height="18" rx="1.5" fill="none" stroke="#fff" stroke-width="1.6"/>
          <rect x="10" y="6" width="4" height="5" fill="#fff"/>
        </svg>
        <span>0437 518 902</span>
      </li>
      <li class="contact__item">
        <svg class="contact__icon" viewBox="0 0 24 24" aria-hidden="true">
          <rect width="24" height="24" fill="var(--ocean)"/>
          <rect x="4" y="6.5" width="16" height="11" fill="none" stroke="#fff" stroke-width="1.6"/>
          <path d="M4 6.5 L12 13 L20 6.5 M4 17.5 L10 12 M20 17.5 L14 12" fill="none" stroke="#fff" stroke-width="1.4"/>
        </svg>
        <span>clara.fenwick@amberLoomSystems.com.au</span>
      </li>
    </ul>
  </section>

</main>
</body>
</html>
```